Corvanth Veylor - Advanced Skincare and undetectable Makeup for Men

We are in need of a professional webpage for our company Corvanth Veylor. We help every man feel his best by looking his best. Inspired by the myth of Corvanth, we offer makeup and skincare products along with education upon their use. Our mission is to celebrate masculinity in all of its forms, regardless of age, race, sexual orientation, or assigned gender at birth.

The webpage would serve as our online store, as a place where our clients can learn about our brand, view our "How-to" video tutorials, and get product information. An online blog will also be hosted in order to keep clients up to date with news, updates, media mentions, etc.

The color schemes that we use are mostly Black and Gold, with Red accents. please keep in mind that this is a men's cosmetics line, and therefore should read powerful, sexy, confident and bold - all with a high end look and feel.

Think along the lines of brands like Lem Brisko, QDV, Belluti, etc.

our logo is included in the files attached. images and copy will be added in at a later time; hence, general images that fit the feel and filler text is encouraged.

The products to be sold include:
a face cleanser in a pump dispenser bottle (1 size)
a mask in a round jar container (1 size)
a moisturizer in a pump container 1 size)
a concealer in a click pen with a brush applicator (3 shades)
a liquid liner pen (4 shades)
a contouring palette (2 shade options)
a setting spray (single option)

Target Market(s)

Millennial Men

Industry/Entity Type

Beauty

Number of Pages Required

5+ page

Font styles to use
Serif

Colors
ec1f27
000000
faa54b

Requirements
Must have
• ur essential requirements are:
• 1) a stunning and engaging landing page that truly captures the ideals of sexuality, boldness and confidence.
• 2) an interactive and engaging online store that is easy to update / add product / information to.
• 3) Product pages supporting various toggling images of the product, a shade selection option, ingredient information, usage instructions, pricing, and a link to a "how to video" unique to each individual product.
• 4) dedicated space where all of the tutorials can be organized together
• 5) an organized Blog section, that would include a segment for a Q&A section for us to update as the brand grows, ongoing contests (that would be easily hidden if there are no contests running at the moment) as well as general news and updates segment.
• 6) an "about us" page, where our customers are able to learn about our story, inspirations, humanitarian efforts and philosophies in product contents and purity.
• 7) a contact us page, which would include social media links, contact email and telephone number as well as physical address to be updated upon launch.
• 8) discrete privacy policy, terms of use, and return policy links available at the bottom of every page
Nice to have
• 1) A posting forum where clients could post their looks using our products, or maybe a live stream of our Pictoval account.
• 2) a member sign in page so that we can collect and store customer information for faster check out, keep track of purchases attached to their email address (future loyalty program plans) and maintain an email database for email notifications and the such.

```html
<!DOCTYPE html>
<html lang="en">
<head>
<meta charset="utf-8">
<title>Corvanth Veylor – Skincare &amp; Makeup for Men</title>
<link rel="stylesheet" href="https://fonts.googleapis.com/css2?family=Marcellus&family=Lato:wght@300;400;700&family=Cormorant+Garamond:ital,wght@0,500;0,600;1,600&display=swap">
<style>
:root{
  --red:#ec1f27;--orange:#faa54b;--gold:#9b7433;--gold-light:#b8924f;
  --black:#000;--ink:#2a2a2a;--muted:#777;--line:#d9d9d9;
  --page:#f3f3f3;--white:#fff;--beige:#ece6df;--footer:#262626;
}
*{margin:0;padding:0;box-sizing:border-box}
html,body{width:1200px;height:4196px;overflow:hidden}
body{position:relative;background:var(--page);font-family:"Lato",sans-serif;color:var(--ink)}
.abs{position:absolute}
.topbar{left:0;top:0;width:1200px;height:50px;background:var(--white);font-size:14px;color:var(--ink)}
.topbar .item{top:16px;display:flex;align-items:center;gap:10px}
.topbar .hl{color:var(--orange);font-weight:700}
.header{left:0;top:50px;width:1200px;height:140px;background:linear-gradient(180deg,#f1ece6,#e6dfd7)}
.brand{left:95px;top:18px;width:170px;text-align:center}
.brand-mark{width:44px;height:44px;margin:0 auto 10px;background:var(--gold)}
.brand-name{font-family:"Marcellus",serif;font-size:16px;letter-spacing:3px;color:var(--gold);white-space:nowrap}
.nav{left:392px;top:43px;display:flex;align-items:center;font-family:"Lato",sans-serif;font-size:15px;color:#555;letter-spacing:.5px}
.nav a{text-decoration:none;color:inherit;padding:0 28px}
.nav a.active{background:var(--gold);color:var(--white);border-radius:26px;height:52px;line-height:52px;padding:0 28px;margin-right:12px}
.search{left:1076px;top:93px;width:44px;height:44px;border:2px solid #888;border-radius:50%}
.hero{left:0;top:190px;width:1200px;height:572px;background:radial-gradient(ellipse at 22% 55%,#7a5a45 0%,#2d211b 30%,#0b0a0a 60%),#000}
.hero-glow{left:820px;top:160px;width:260px;height:400px;border-radius:30px;background:linear-gradient(180deg,#6a4f3c,#3a2a22);opacity:.9}
.section-title{left:0;width:1200px;text-align:center;font-family:"Cormorant Garamond",serif;font-weight:500;font-size:54px;letter-spacing:1px;color:var(--red)}
.section-title span{color:var(--orange)}
.tabs{left:0;top:904px;width:1200px;text-align:center;font-family:"Cormorant Garamond",serif;font-size:19px;color:#999}
.tabs b{color:var(--ink);text-decoration:underline;font-weight:600}
.tabs i{font-style:normal;margin:0 16px}
.card{width:252px}
.card .photo{height:257px;background:var(--white);position:relative}
.card .photo .shot{position:absolute;left:36px;top:30px;right:36px;bottom:30px;border-radius:6px}
.card .name{height:48px;margin-top:30px;font-size:17px;line-height:23px;text-align:center;display:flex;align-items:center;justify-content:center;padding:0 14px}
.card .price{margin-top:12px;text-align:center;font-family:"Cormorant Garamond",serif;font-size:30px;color:#777}
.card .stars{margin-top:4px;text-align:center;color:#f2b21c;font-size:21px;letter-spacing:2px}
.quick{position:absolute;right:0;top:0;width:34px}
.quick div{height:34px;background:var(--red);margin-bottom:3px;display:flex;align-items:center;justify-content:center}
.offer{left:78px;top:1866px;width:1042px;height:539px;background:linear-gradient(90deg,#8a7e72,#cfc6ba 50%,#9a9087)}
.offer-panel{left:20px;top:16px;width:1007px;height:509px;background:linear-gradient(100deg,#c9975e 0%,#e3b884 45%,#d3a774 100%);border:2px solid #f0d4ae}
.offer-text{left:52px;top:300px;color:var(--white)}
.offer-text h3{font-family:"Cormorant Garamond",serif;font-weight:600;font-size:48px;letter-spacing:1px}
.offer-text p{font-size:17px;line-height:24px;width:420px;margin-top:6px}
.offer-text a{display:inline-block;margin-top:18px;font-family:"Cormorant Garamond",serif;font-style:italic;font-weight:600;font-size:28px;color:var(--white);text-decoration:underline}
.faq{left:280px;width:642px;background:var(--white);border:1px solid var(--line)}
.faq .q{font-family:"Cormorant Garamond",serif;font-size:16px;color:#333;padding:0 36px 0 22px;height:40px;line-height:40px;position:relative}
.faq .ic{position:absolute;right:12px;top:12px;width:16px;height:16px;border-radius:50%}
.faq .a{padding:0 40px 0 36px;font-size:13px;line-height:19px;color:#888}
.faq .more{display:inline-block;margin:14px 0 0 36px;font-size:14px;font-weight:700;color:var(--red);text-decoration:underline;letter-spacing:.5px}
.post{top:3160px;width:480px}
.post .date{position:absolute;left:0;top:0;width:62px;height:68px;background:var(--orange);color:var(--white);text-align:center;font-family:"Cormorant Garamond",serif}
.post .date b{display:block;font-size:30px;line-height:42px}
.post .date small{font-family:"Lato",sans-serif;font-size:12px}
.post .body{margin-left:96px}
.post h4{font-family:"Cormorant Garamond",serif;font-weight:600;font-size:17px;letter-spacing:.5px}
.post p{font-size:13px;line-height:20px;color:#555;margin-top:8px}
.post a{display:inline-block;margin-top:14px;font-family:"Cormorant Garamond",serif;font-weight:600;font-size:15px;color:#333;text-decoration:none;border-bottom:1px solid #333;padding-bottom:4px}
.divider{left:78px;top:3348px;width:1042px;height:1px;background:var(--line)}
.arrow{top:3378px;width:40px;height:40px;border-radius:50%;display:flex;align-items:center;justify-content:center}
.newsletter{left:0;top:3518px;width:1200px;height:314px;background:var(--white)}
.newsletter p{position:absolute;left:280px;top:140px;width:640px;text-align:center;font-size:14px;line-height:22px;color:#c8c8c8}
.field{left:313px;top:199px;width:568px;height:45px;border:1px solid #ccc;background:var(--white)}
.field span{position:absolute;left:28px;top:13px;font-size:13px;color:#bbb}
.field .send{position:absolute;right:-1px;top:-1px;width:46px;height:45px;background:var(--black);display:flex;align-items:center;justify-content:center}
.footer{left:0;top:3832px;width:1200px;height:364px;background:linear-gradient(120deg,#2e2e2e,#1e1e1e 60%,#2a2a2a);color:#ddd}
.footer h5{font-family:"Cormorant Garamond",serif;font-weight:600;font-size:22px;color:var(--white)}
.footer ul{list-style:none;margin-top:14px;font-size:13px;line-height:25px;color:#ccc}
.foot-about{left:78px;top:32px;width:200px;text-align:center}
.foot-about .brand-mark{width:38px;height:38px;margin-bottom:10px}
.foot-about .brand-name{font-size:13px;letter-spacing:2px}
.foot-about p{margin-top:10px;font-size:13px;line-height:18px;text-align:left;color:#ccc}
.cards{margin-top:12px;display:grid;grid-template-columns:repeat(4,44px);gap:6px}
.cards div{height:26px;background:#f2f2f2;border-radius:3px}
.contact-row{display:flex;align-items:center;gap:12px;font-size:13px;color:#ccc;margin-top:14px}
.social{display:flex;gap:12px;margin-top:22px}
.social div{width:38px;height:38px;border-radius:50%}
.foot-line{left:78px;top:299px;width:1042px;height:1px;background:#555}
.copyright{left:0;top:322px;width:1200px;text-align:center;font-size:12px;color:#bbb}
.copyright b{color:var(--orange);font-family:"Marcellus",serif;font-weight:400;letter-spacing:1px}
</style>
</head>
<body>

<div class="abs topbar">
  <div class="abs item" style="left:78px">
    <svg width="16" height="16" viewBox="0 0 24 24"><path d="M6.6 10.8a15 15 0 0 0 6.6 6.6l2.2-2.2c.3-.3.7-.4 1-.2 1.1.4 2.3.6 3.6.6.6 0 1 .4 1 1V20c0 .6-.4 1-1 1A17 17 0 0 1 3 4c0-.6.4-1 1-1h3.5c.6 0 1 .4 1 1 0 1.3.2 2.5.6 3.6.1.3 0 .7-.2 1z" fill="#222"/></svg>
    <span>Call Us : <span class="hl">555-010-2048</span></span>
  </div>
  <div class="abs item" style="left:335px">
    <svg width="16" height="16" viewBox="0 0 24 24"><circle cx="12" cy="7" r="5" fill="#222"/><path d="M2 23c0-6 4.5-9 10-9s10 3 10 9z" fill="#222"/></svg>
    <span>Mail Us : <span class="hl">admin@corvanthveylor.com</span></span>
  </div>
  <div class="abs item" style="left:895px">
    <svg width="20" height="18" viewBox="0 0 24 22"><path d="M1 2h4l3 12h12l3-9H7" fill="none" stroke="#222" stroke-width="2"/><circle cx="9" cy="19" r="2" fill="#222"/><circle cx="19" cy="19" r="2" fill="#222"/></svg>
    <span>Cart | 0 | Items &nbsp;&nbsp;|&nbsp;&nbsp; $0.00</span>
  </div>
</div>

<header class="abs header">
  <div class="abs brand">
    <div class="brand-mark"></div>
    <div class="brand-name">CORVANTH VEYLOR</div>
  </div>
  <nav class="abs nav">
    <a class="active" href="#">HOME</a>
    <a href="#">ABOUT US</a>
    <a href="#">PRODUCTS</a>
    <a href="#">BLOG</a>
    <a href="#">CONTACT</a>
  </nav>
  <div class="abs search" style="top:43px">
    <svg width="40" height="40" viewBox="0 0 40 40"><circle cx="18" cy="18" r="7" fill="none" stroke="#777" stroke-width="2"/><path d="M23 23l6 6" stroke="#777" stroke-width="2"/></svg>
  </div>
</header>

<section class="abs hero" role="img" aria-label="Groomed man with stubble beside a tube of men's face product on a dark backdrop">
  <div class="abs hero-glow"></div>
</section>

<h2 class="abs section-title" style="top:826px">OUR <span>PRODUCTS</span></h2>
<div class="abs tabs"><b>Latest</b><i>/</i>Brand<i>/</i>Special</div>

<div class="abs card" style="left:78px;top:965px"><div class="photo"><div class="shot" role="img" aria-label="Face cleanser in a pump dispenser bottle" style="background:linear-gradient(180deg,#e8e8e8,#b9bcc0)"></div></div><div class="name">A in a Pump Dispenser Bottle</div><div class="price">$ 80.00</div><div class="stars">★★★★★</div></div>
<div class="abs card" style="left:341px;top:965px"><div class="photo"><div class="shot" role="img" aria-label="Mask in a round jar container" style="background:radial-gradient(circle,#e7d3b8,#c9b49a 60%,#f2ece6)"></div></div><div class="name">A Mask in a Round Jar Container</div><div class="price">$ 80.00</div><div class="stars">★★★★★</div></div>
<div class="abs card" style="left:604px;top:965px"><div class="photo"><div class="shot" role="img" aria-label="Moisturizer bottles in pump containers" style="background:linear-gradient(180deg,#f3f6f6,#cfe2e2)"></div>
  <div class="quick">
    <div><svg width="18" height="16" viewBox="0 0 24 22"><path d="M1 2h4l3 12h12l3-9H7" fill="none" stroke="#fff" stroke-width="2"/><circle cx="9" cy="19" r="2" fill="#fff"/><circle cx="19" cy="19" r="2" fill="#fff"/></svg></div>
    <div><svg width="18" height="16" viewBox="0 0 24 22"><path d="M12 20S2 13.5 2 7.5A5 5 0 0 1 12 5a5 5 0 0 1 10 2.5C22 13.5 12 20 12 20z" fill="none" stroke="#fff" stroke-width="2"/></svg></div>
    <div><svg width="20" height="14" viewBox="0 0 24 16"><path d="M1 8s4-7 11-7 11 7 11 7-4 7-11 7S1 8 1 8z" fill="none" stroke="#fff" stroke-width="2"/><circle cx="12" cy="8" r="3" fill="#fff"/></svg></div>
    <div><svg width="18" height="16" viewBox="0 0 24 20"><path d="M2 6h18l-4-4M22 14H4l4 4" fill="none" stroke="#fff" stroke-width="2"/></svg></div>
  </div></div><div class="name">A Moisturizer in a Pump Container</div><div class="price">$ 80.00</div><div class="stars">★★★★★</div></div>
<div class="abs card" style="left:867px;top:965px"><div class="photo"><div class="shot" role="img" aria-label="Concealer click pens with brush applicators" style="background:linear-gradient(135deg,#f5efe8,#5a3e2e 55%,#d8b88a)"></div></div><div class="name">A Concealer in a Click Pen with a Brush Applicator</div><div class="price">$ 80.00</div><div class="stars">★★★★★</div></div>

<div class="abs card" style="left:78px;top:1398px"><div class="photo"><div class="shot" role="img" aria-label="Two tubes of men's face cleanser" style="background:linear-gradient(90deg,#d59a47,#3d3532)"></div></div><div class="name" style="margin-top:24px">A in a Pump Dispenser Bottle</div><div class="price">$ 80.00</div><div class="stars">★★★★★</div></div>
<div class="abs card" style="left:341px;top:1398px"><div class="photo"><div class="shot" role="img" aria-label="Setting spray bottle" style="background:linear-gradient(180deg,#2c2522,#4a3a33)"></div></div><div class="name" style="margin-top:24px">A Setting Spray</div><div class="price">$ 80.00</div><div class="stars">★★★★★</div></div>
<div class="abs card" style="left:604px;top:1398px"><div class="photo"><div class="shot" role="img" aria-label="Open contouring palette" style="background:linear-gradient(135deg,#2a2220,#7b5a48 50%,#e4d49a)"></div></div><div class="name" style="margin-top:24px">A Contouring Palette</div><div class="price">$ 80.00</div><div class="stars">★★★★★</div></div>
<div class="abs card" style="left:867px;top:1398px"><div class="photo"><div class="shot" role="img" aria-label="Liquid liner pens" style="background:linear-gradient(90deg,#fff,#1a1a1a 30%,#fff 50%,#1a1a1a 75%,#fff)"></div></div><div class="name" style="margin-top:24px">A Liquid Liner Pen</div><div class="price">$ 80.00</div><div class="stars">★★★★★</div></div>

<section class="abs offer">
  <div class="abs offer-panel" role="img" aria-label="Man on a beach beside a row of men's grooming tubes, sepia toned"></div>
  <div class="abs offer-text">
    <h3>SPECIAL OFFER</h3>
    <p>Lorem Ipsum is simply dummy text of the printing and typesetting industry.</p>
    <a href="#">SHOP NOW</a>
  </div>
</section>

<h2 class="abs section-title" style="top:2474px">FAQ's</h2>
<div class="abs faq" style="top:2562px;height:157px">
  <div class="q" style="height:48px;line-height:48px">Lorem Ipsum is simply dummy text of the printing.
    <svg class="ic" style="top:16px" viewBox="0 0 16 16"><circle cx="8" cy="8" r="8" fill="#ec1f27"/><path d="M5 5l6 6M11 5l-6 6" stroke="#fff" stroke-width="1.6"/></svg></div>
  <div class="a">Lorem Ipsum is simply dummy text of the printing and typesetting industry. Lorem Ipsum has been the industry's standard dummy text ever since the 1500s.</div>
  <a class="more" href="#">READ MORE</a>
</div>
<div class="abs faq" style="top:2738px"><div class="q">Lorem Ipsum is simply dummy text.<svg class="ic" viewBox="0 0 16 16"><circle cx="8" cy="8" r="8" fill="#333"/><path d="M5 8h6M9 5l3 3-3 3" stroke="#fff" stroke-width="1.6" fill="none"/></svg></div></div>
<div class="abs faq" style="top:2794px"><div class="q">Lorem Ipsum is simply dummy text of the printing.<svg class="ic" viewBox="0 0 16 16"><circle cx="8" cy="8" r="8" fill="#333"/><path d="M5 8h6M9 5l3 3-3 3" stroke="#fff" stroke-width="1.6" fill="none"/></svg></div></div>
<div class="abs faq" style="top:2850px"><div class="q">Lorem Ipsum is simply dummy text of the typesetting.<svg class="ic" viewBox="0 0 16 16"><circle cx="8" cy="8" r="8" fill="#333"/><path d="M5 8h6M9 5l3 3-3 3" stroke="#fff" stroke-width="1.6" fill="none"/></svg></div></div>
<div class="abs faq" style="top:2906px"><div class="q">Lorem Ipsum is simply dummy text.<svg class="ic" viewBox="0 0 16 16"><circle cx="8" cy="8" r="8" fill="#333"/><path d="M5 8h6M9 5l3 3-3 3" stroke="#fff" stroke-width="1.6" fill="none"/></svg></div></div>
<div class="abs faq" style="top:2962px"><div class="q">Lorem Ipsum is simply DUMMY text.<svg class="ic" viewBox="0 0 16 16"><circle cx="8" cy="8" r="8" fill="#333"/><path d="M5 8h6M9 5l3 3-3 3" stroke="#fff" stroke-width="1.6" fill="none"/></svg></div></div>

<h2 class="abs section-title" style="top:3073px">FROM THE <span>BLOG</span></h2>
<article class="abs post" style="left:98px">
  <div class="date"><b>21</b><small>July</small></div>
  <div class="body">
    <h4>LOREM IPSUM DUMMY</h4>
    <p>Lorem Ipsum is simply dummy text of the printing and typesetting industry. Lorem Ipsum has been the industry's standard dummy text ever since the 1500s.</p>
    <a href="#">READ MORE»</a>
  </div>
</article>
<article class="abs post" style="left:630px">
  <div class="date"><b>21</b><small>July</small></div>
  <div class="body">
    <h4>LOREM IPSUM DUMMY</h4>
    <p>Lorem Ipsum is simply dummy text of the printing and typesetting industry. Lorem Ipsum has been the industry's standard dummy text ever since the 1500s.</p>
    <a href="#">READ MORE»</a>
  </div>
</article>
<div class="abs divider"></div>
<div class="abs arrow" style="left:550px;background:#3a3a3a"><svg width="14" height="14" viewBox="0 0 14 14"><path d="M9 2L4 7l5 5" stroke="#fff" stroke-width="2" fill="none"/></svg></div>
<div class="abs arrow" style="left:606px;background:var(--orange)"><svg width="14" height="14" viewBox="0 0 14 14"><path d="M5 2l5 5-5 5" stroke="#fff" stroke-width="2" fill="none"/></svg></div>

<section class="abs newsletter">
  <h2 class="abs section-title" style="top:58px">SUBSCRIBE <span>NEWSLETTER</span></h2>
  <p>Lorem Ipsum is simply dummy text of the printing and typesetting industry. Lorem Ipsum has been the industry's standard text.</p>
  <div class="abs field">
    <svg style="position:absolute;left:10px;top:17px" width="12" height="10" viewBox="0 0 12 10"><rect width="12" height="10" fill="#999"/></svg>
    <span>Email</span>
    <div class="send"><svg width="18" height="18" viewBox="0 0 24 24"><path d="M22 2L2 10l8 3 3 9z M10 13l12-11" fill="none" stroke="#fff" stroke-width="1.8"/></svg></div>
  </div>
</section>

<footer class="abs footer">
  <div class="abs foot-about">
    <div class="brand-mark"></div>
    <div class="brand-name">CORVANTH VEYLOR</div>
    <p>Lorem Ipsum is simply dummy text of the printing and typesetting industry Lorem Ipsum has.</p>
    <div class="cards"><div></div><div></div><div></div><div></div><div></div><div></div><div></div><div></div></div>
  </div>
  <div class="abs" style="left:352px;top:62px"><h5>Usefull Links</h5><ul><li>Home</li><li>About Us</li><li>Products</li><li>Buy Online</li><li>Blogs</li><li>Contact Us</li></ul></div>
  <div class="abs" style="left:604px;top:62px"><h5>Need Help</h5><ul><li>Help</li><li>Site Map</li><li>Contact Form</li><li>Forgot Password</li></ul></div>
  <div class="abs" style="left:870px;top:62px"><h5>Keep In Touch</h5>
    <div class="contact-row"><svg width="16" height="16" viewBox="0 0 24 24"><path d="M6.6 10.8a15 15 0 0 0 6.6 6.6l2.2-2.2c.3-.3.7-.4 1-.2 1.1.4 2.3.6 3.6.6.6 0 1 .4 1 1V20c0 .6-.4 1-1 1A17 17 0 0 1 3 4c0-.6.4-1 1-1h3.5c.6 0 1 .4 1 1 0 1.3.2 2.5.6 3.6.1.3 0 .7-.2 1z" fill="#faa54b"/></svg>555 010 2049</div>
    <div class="contact-row"><svg width="16" height="12" viewBox="0 0 16 12"><rect width="16" height="12" fill="#faa54b"/><path d="M0 0l8 6 8-6" stroke="#262626" stroke-width="1.4" fill="none"/></svg>info@CORVANTHVEYLOR.com</div>
    <div class="social"><div style="background:var(--orange)"></div><div style="border:2px solid #ddd"></div></div>
  </div>
  <div class="abs foot-line"></div>
  <div class="abs copyright">© 2018 <b>CORVANTH VEYLOR</b> - All rights reserved</div>
</footer>

</body>
</html>
```